Brookvane Consulting Business Card Design

Business Card Design for Brookvane Consulting. Brookvane Consulting is a boutique consultancy based in Atlanta, GA., that specializes in marketing strategy, organization planning, and leadership development. We provide solutions for small businesses and startups as well as Vantage 300 companies.

http://brookvaneconsulting.com/

Target Market(s)

We provide solutions for small businesses and startups as well as Vantage 300 companies.

Industry/Entity Type

Consulting

Contact Information for Business Card

Two sided business card with priority on contact information, logo, tag line (Inspiration to Dream More, Do More, Become More)

Colors

Designer to choose colors to be used in the design.

Requirements
Must have
• contact information, logo, tag line (Inspiration to Dream More, Do More, Become More)
• Simple no over communication.
Nice to have
• I would like to see different placements of logo and creative use of both sides of the card
Should not have
• Do not put too much information on the card.

```html
<!DOCTYPE html>
<html lang="en">
<head>
<meta charset="utf-8">
<title>Brookvane Consulting Business Card</title>
<link href="https://fonts.googleapis.com/css2?family=Lato:wght@300;400;700&family=Arimo:wght@700&display=swap" rel="stylesheet">
<style>
  :root {
    --charcoal: #363636;
    --paper: #ffffff;
    --ink: #2b2b2b;
    --muted: #555555;
    --soft: #cfcfcf;
    --stage: #e6e4e1;
  }
  html, body {
    margin: 0;
    padding: 0;
    width: 1200px;
    height: 930px;
    overflow: hidden;
    background: var(--stage);
    font-family: "Lato", sans-serif;
  }
  .canvas { position: relative; width: 1200px; height: 930px; }
  .card {
    position: absolute;
    left: 250px;
    width: 700px;
    height: 400px;
    border-radius: 22px;
    overflow: hidden;
    box-shadow: 0 6px 18px rgba(0,0,0,0.18);
  }
  .card-front {
    top: 45px;
    background: var(--charcoal);
    display: flex;
    flex-direction: column;
    align-items: center;
    justify-content: center;
    gap: 18px;
  }
  .card-back { top: 485px; background: var(--paper); }
  .brand {
    display: flex;
    align-items: center;
    gap: 14px;
    font-family: "Lato", sans-serif;
    font-weight: 700;
    letter-spacing: 0.5px;
  }
  .brand-mark { width: 18px; height: 18px; }
  .card-front .brand { color: var(--paper); font-size: 46px; }
  .card-front .brand-mark { background: var(--paper); }
  .tagline {
    margin: 0;
    font-size: 17px;
    font-weight: 300;
    letter-spacing: 1.5px;
    color: var(--soft);
  }
  .card-back .brand {
    position: absolute;
    left: 48px;
    top: 150px;
    color: var(--ink);
    font-size: 32px;
  }
  .card-back .brand-mark { background: var(--ink); width: 14px; height: 14px; }
  .person { position: absolute; right: 40px; top: 52px; text-align: right; }
  .person-name {
    font-family: "Arimo", sans-serif;
    font-weight: 700;
    font-size: 27px;
    color: var(--ink);
    margin: 0;
  }
  .person-title { font-size: 16px; font-weight: 300; color: var(--muted); margin: 2px 0 0; }
  .rule { position: absolute; height: 1.5px; background: var(--ink); }
  .rule-top { left: 250px; right: 40px; top: 118px; }
  .rule-contact { left: 40px; width: 430px; top: 270px; }
  .address {
    position: absolute;
    right: 40px;
    top: 138px;
    text-align: right;
    font-size: 16px;
    font-weight: 300;
    color: var(--muted);
    line-height: 1.35;
  }
  .contacts {
    position: absolute;
    left: 40px;
    top: 282px;
    margin: 0;
    padding: 0;
    list-style: none;
    font-size: 17px;
    font-weight: 300;
    color: var(--ink);
    line-height: 1.3;
  }
  .contacts li { display: flex; align-items: center; gap: 10px; }
  .contacts svg { width: 12px; height: 12px; fill: var(--ink); flex: none; }
  .accent-band { position: absolute; inset: 0; width: 700px; height: 400px; }
</style>
</head>
<body>
<div class="canvas">

  <section class="card card-front" aria-label="Card front">
    <div class="brand"><span class="brand-mark"></span>Brookvane Consulting</div>
    <p class="tagline">Inspiration to Dream More, Do More, Become More</p>
  </section>

  <section class="card card-back" aria-label="Card back">
    <svg class="accent-band" viewBox="0 0 700 400" aria-hidden="true">
      <polygon points="455,400 468,292 700,292 700,400" fill="#363636"/>
      <polygon points="478,400 488,300 494,300 484,400" fill="#ffffff"/>
    </svg>

    <div class="brand"><span class="brand-mark"></span>Brookvane Consulting</div>

    <div class="person">
      <p class="person-name">DANIEL REYES</p>
      <p class="person-title">Director</p>
    </div>
    <div class="rule rule-top"></div>

    <div class="address">1180 Halden Street NE,<br>Atlanta, GA 30309</div>

    <div class="rule rule-contact"></div>
    <ul class="contacts">
      <li><svg viewBox="0 0 12 12"><path d="M2 0.5l2.2 0.3 0.8 2.6-1.3 1a6 6 0 0 0 3 3l1-1.3 2.6 0.8 0.3 2.2-1.4 1.4C4.6 10.2 1.8 7.4 0.6 1.9z"/></svg>+1 404 555-0142</li>
      <li><svg viewBox="0 0 12 12"><path d="M3 0h6v12H3zM4 1v8.5h4V1zM5.5 10.2h1v1h-1z" fill-rule="evenodd"/></svg>+1 404 555-0187</li>
      <li><svg viewBox="0 0 12 12"><path d="M0 2h12v8H0zM1 3v0.4l5 3.2 5-3.2V3zM1 4.6V9h10V4.6L6 7.8z" fill-rule="evenodd"/></svg>info@BrookvaneConsulting.com</li>
      <li><svg viewBox="0 0 12 12"><circle cx="6" cy="6" r="6"/></svg>www.BrookvaneConsulting.com</li>
    </ul>
  </section>

</div>
</body>
</html>
```